International Book about Player ethics in stadiums - This book will be presented to players in all

This book will be distributed to players to learn about the mathematical ethics, and the spirit of sport required for the ideal player
It also aims to teach the public the morals of encouragement and some instructions about keeping the playgrounds beautiful
Size : w 15 x 21 H
Title of the book
نجوم على ضفاف الغروب
Author
تاليف / الدكتور ناصر بن عيسى المرزوقي
1440-2018

Target Market(s)

This book will be presented to players in all activities

Colors

Designer to choose colors to be used in the design.

Requirements
Must have
• Selected colors must be related to play, players, activity and vitality.
• To be the attractive design makes the book lovable
• Final design of the file in the front and back should be on files illustrator and Photoshop and accept the opening on the lower versions
•  
Nice to have
• Example:
• Option 1
• stadium image
• The image must be for a mathematical expression
• For example: a player extends his hand to the opponent to help him from the ground or
• Two players from the two teams are hugging - shaking hands
• Option 2
• The picture can be a sports track
• On both sides of the track are the names of sports ethics - fair play - sportsmanship - compassion - clean encouragement - discipline - respect - apology ... etc
Should not have
• Direct images of famous players or people
• In the case of images should be indirect - or possible to be drawings
• Direct photos of famous people or players are not required

```html
<!DOCTYPE html>
<html lang="ar" dir="rtl">
<head>
<meta charset="utf-8">
<title>نجوم على ضفاف الغروب</title>
<link rel="stylesheet" href="https://fonts.googleapis.com/css2?family=Cairo:wght@700;900&display=swap">
<style>
  :root {
    --page-bg: #dcedf8;
    --cover-red: #4a0205;
    --cover-red-deep: #2a0002;
    --cover-red-glow: #5e0a0e;
    --title-fill: #12304a;
    --title-edge: #ffffff;
    --author-text: #ffffff;
    --sky-top: #3a2a4a;
    --sky-mid: #c98a5a;
    --sky-glow: #f3e2c8;
    --stands: #4d3a6a;
    --pitch: #4f7a3c;
  }
  html, body {
    margin: 0;
    width: 1200px;
    height: 1200px;
    overflow: hidden;
    background: var(--page-bg);
  }
  .stage {
    position: relative;
    width: 1200px;
    height: 1200px;
  }
  .book-cover {
    position: absolute;
    left: 328px;
    top: 192px;
    width: 552px;
    height: 826px;
    overflow: hidden;
    background: radial-gradient(ellipse at 50% 75%, var(--cover-red-glow) 0%, var(--cover-red) 45%, var(--cover-red-deep) 100%);
    font-family: "Cairo", sans-serif;
  }
  .cover-photo {
    position: absolute;
    left: 0;
    top: 0;
    width: 552px;
    height: 480px;
    display: block;
  }
  .cover-title {
    position: absolute;
    left: 0;
    right: 0;
    top: 505px;
    margin: 0;
    text-align: center;
    font-weight: 900;
    font-size: 70px;
    line-height: 96px;
    color: var(--title-fill);
    -webkit-text-stroke: 3px var(--title-edge);
    paint-order: stroke fill;
    text-shadow: 0 4px 10px rgba(0,0,0,0.6);
  }
  .cover-author {
    position: absolute;
    left: 0;
    right: 0;
    top: 748px;
    margin: 0;
    text-align: center;
    font-weight: 700;
    font-size: 21px;
    color: var(--author-text);
  }
</style>
</head>
<body>
<div class="stage">
  <div class="book-cover">
    <svg class="cover-photo" viewBox="0 0 552 480" role="img" aria-label="ملعب رياضي ليلي بأضواء كاشفة وسماء الغروب والعشب الأخضر">
      <defs>
        <linearGradient id="stadiumScene" x1="0" y1="0" x2="0" y2="1">
          <stop offset="0" stop-color="var(--sky-top)"/>
          <stop offset="0.25" stop-color="var(--sky-mid)"/>
          <stop offset="0.5" stop-color="var(--stands)"/>
          <stop offset="0.78" stop-color="var(--stands)"/>
          <stop offset="0.8" stop-color="var(--pitch)"/>
          <stop offset="0.9" stop-color="var(--pitch)"/>
          <stop offset="1" stop-color="var(--cover-red)"/>
        </linearGradient>
        <radialGradient id="floodGlow" cx="0.72" cy="0.42" r="0.45">
          <stop offset="0" stop-color="var(--sky-glow)" stop-opacity="0.85"/>
          <stop offset="1" stop-color="var(--sky-glow)" stop-opacity="0"/>
        </radialGradient>
      </defs>
      <rect width="552" height="480" fill="url(#stadiumScene)"/>
      <rect width="552" height="480" fill="url(#floodGlow)"/>
    </svg>
    <h1 class="cover-title">نجوم على<br>ضفاف الغروب</h1>
    <p class="cover-author">المؤلف/الدكتور ناصر بن عيسى المرزوقي</p>
  </div>
</div>
</body>
</html>
```